Dynamic Business Card for Sports Supplements Company

Hi! I'm looking for an awesome business card to match my existing sports supplement company. I have uploaded my current company logo and screenshot of the front page of my website.

I would like to have something dynamic and interesting and utilize the colors in the website - the reds and purples

The business card should be double sided and focus on a unique eye-catching design on the back and include all the relevant company info.

Most importantly, it should say somewhere: "Sign up on our website for a coupon code."

Target Market(s)

Mostly for women gym goers but it shouldn't be too feminine. It should be in keeping with the website design. It should flow and clearly be connected to it

Industry/Entity Type

Business

Contact Information for Business Card

Lorraine K. Vestal
CEO
LVestal@Quorvanexco.com
www.quorvanexco.com
555.417.3820
P.O. Box 47315
Alder Falls, Oregon 00000

Sign up on our website for a coupon code

Font styles to use
Serif
Sans Serif
Other font styles liked:
• Novecento font family and "Quorvanex" is in AR Destine font

Requirements
Must have
• One side should be a bold Quorvanex logo design. Even just the symbol itself may be o.k. (see attached file)

```html
<!DOCTYPE html>
<html lang="en">
<head>
<meta charset="utf-8">
<title>Quorvanex Business Card</title>
<link href="https://fonts.googleapis.com/css2?family=Montserrat:wght@400;500;700;800&display=swap" rel="stylesheet">
<style>
  :root {
    --backdrop: #3a3a3a;
    --card: #050505;
    --white: #ffffff;
    --red: #e5202a;
    --rule: #9a9a9a;
  }
  * { margin: 0; padding: 0; box-sizing: border-box; }
  html, body { width: 1200px; height: 855px; overflow: hidden; }
  body {
    background: var(--backdrop);
    font-family: "Montserrat", sans-serif;
    color: var(--white);
    display: flex;
    align-items: center;
    justify-content: center;
    gap: 40px;
  }
  .card {
    width: 540px;
    height: 309px;
    background: var(--card);
    position: relative;
    box-shadow: 0 14px 30px rgba(0,0,0,.45);
  }
  .brand { display: flex; flex-direction: column; align-items: center; }
  .brand-name {
    font-weight: 800; font-size: 40px; letter-spacing: 1px; line-height: 1;
  }
  .brand-tagline {
    font-size: 11.5px; letter-spacing: 2.2px; margin-top: 6px; text-transform: uppercase;
  }

  .card-front { display: flex; flex-direction: column; align-items: center; justify-content: center; }
  .card-front .brand { margin-top: -10px; }
  .signup { font-size: 14px; margin-top: 44px; letter-spacing: .3px; }
  .signup .accent { color: var(--red); }

  .card-back { display: flex; align-items: center; }
  .card-back .brand { width: 270px; padding-top: 40px; }
  .card-back .brand-name { font-size: 31px; }
  .card-back .brand-tagline { font-size: 9.5px; letter-spacing: 1.6px; }
  .divider { width: 1px; height: 158px; background: var(--rule); }
  .contact { padding-left: 24px; font-size: 14px; line-height: 1.3; }
  .contact-name { color: var(--red); font-size: 20px; font-weight: 500; letter-spacing: .3px; }
  .contact-title { margin-bottom: 14px; }
  .contact-address { margin-bottom: 12px; padding-left: 8px; }
  .contact-list { list-style: none; padding-left: 8px; }
  .contact-list li { display: flex; align-items: center; gap: 8px; font-size: 13.5px; }
  .contact-list svg { width: 11px; height: 11px; flex: none; }
</style>
</head>
<body>
  <section class="card card-front">
    <div class="brand">
      <div class="brand-name">QUORVANEX</div>
      <div class="brand-tagline">Your Strength Companion</div>
    </div>
    <p class="signup">Sign up on our website <span class="accent">for a coupon code</span></p>
  </section>

  <section class="card card-back">
    <div class="brand">
      <div class="brand-name">QUORVANEX</div>
      <div class="brand-tagline">Your Strength Companion</div>
    </div>
    <div class="divider"></div>
    <div class="contact">
      <div class="contact-name">Lorraine K. Vestal</div>
      <div class="contact-title">CEO</div>
      <div class="contact-address">P.O. Box 47315<br>Alder Falls, Oregon 00000</div>
      <ul class="contact-list">
        <li>
          <svg viewBox="0 0 12 12"><path d="M2.5 1 4.5 3 3.5 4.5Q5 7.5 7.5 8.5L9 7.5 11 9.5 9.5 11Q3 10 1 2.5Z" fill="var(--red)"/></svg>
          555.417.3820
        </li>
        <li>
          <svg viewBox="0 0 12 12"><rect x="1" y="2.5" width="10" height="7" fill="var(--red)"/><path d="M1 2.5 6 6.5 11 2.5" stroke="var(--card)" fill="none"/></svg>
          LVestal@Quorvanexco.com
        </li>
        <li>
          <svg viewBox="0 0 12 12" fill="none" stroke="var(--red)" stroke-width="1.1"><circle cx="6" cy="6" r="5"/><ellipse cx="6" cy="6" rx="2.2" ry="5"/><path d="M1 6H11"/></svg>
          www.quorvanexco.com
        </li>
      </ul>
    </div>
  </section>
</body>
</html>
```